Woman owned consulting company needs an elegant and modern business card design

I need a business card design for my new consulting company, Mara Quillon Consulting. I am looking for something that is simple and elegant, but also creative and original. You can use either version of the logo that are attached. I have also included the information that needs to be featured on the business card.

Contact Information for Business Card

Requirements
Must have
• The logo and the font type and a standard business card size. Use shades of gray/silver and or rose gold that are in the logo.
• I didn't realize that my actual logo wasn't attached. Please incorporate in the designs.
Should not have
• Colors that are different from my logo

```html
<!DOCTYPE html>
<html lang="en">
<head>
<meta charset="UTF-8">
<title>Mara Quillon Consulting – Business Card</title>
<link href="https://fonts.googleapis.com/css2?family=Cinzel:wght@400;700&family=Lora:wght@400&display=swap" rel="stylesheet">
<style>
  :root {
    --backdrop: #3b3b3d;
    --card: #202123;
    --silver: #c9cacc;
    --silver-dim: #8e9093;
    --white: #f2f2f2;
    --band-dark: #3d4246;
    --band-light: #b9babb;
  }
  * { box-sizing: border-box; margin: 0; padding: 0; }
  html, body { width: 799px; height: 1200px; overflow: hidden; }
  body {
    background: var(--backdrop);
    display: flex;
    flex-direction: column;
    align-items: center;
    justify-content: space-around;
    padding: 80px 0;
  }
  .card {
    position: relative;
    width: 640px;
    height: 366px;
    background: var(--card);
    overflow: hidden;
    box-shadow: 0 14px 30px rgba(0,0,0,0.45);
  }
  /* Front */
  .card-front {
    display: flex;
    align-items: center;
    justify-content: center;
  }
  .front-wordmark {
    font-family: "Cinzel", serif;
    font-weight: 400;
    font-size: 34px;
    letter-spacing: 3px;
    color: var(--silver);
    text-align: center;
    line-height: 1.25;
  }
  /* Back */
  .brand-line {
    position: absolute;
    left: 36px;
    top: 36px;
    font-family: "Cinzel", serif;
    font-weight: 400;
    font-size: 30px;
    line-height: 1.1;
    color: var(--silver);
    letter-spacing: 1px;
  }
  .person {
    position: absolute;
    left: 36px;
    top: 150px;
  }
  .person-name {
    font-family: "Cinzel", serif;
    font-weight: 700;
    font-size: 20px;
    color: var(--white);
    letter-spacing: 1px;
  }
  .person-role {
    font-family: "Lora", serif;
    font-size: 13px;
    color: var(--silver-dim);
    margin-top: 2px;
  }
  .contact-list {
    position: absolute;
    left: 356px;
    top: 190px;
    list-style: none;
    font-family: "Lora", serif;
    font-size: 14px;
    color: var(--silver);
  }
  .contact-list li {
    display: flex;
    align-items: center;
    gap: 10px;
    height: 22px;
  }
  .contact-list svg { width: 14px; height: 14px; fill: var(--silver); }
  .bottom-bands {
    position: absolute;
    left: 0;
    bottom: 0;
    width: 640px;
    height: 100px;
  }
  .band-label {
    position: absolute;
    right: 34px;
    bottom: 20px;
    font-family: "Cinzel", serif;
    font-size: 17px;
    color: var(--white);
    letter-spacing: 1px;
  }
</style>
</head>
<body>
  <section class="card card-front">
    <p class="front-wordmark">Mara Quillon<br>Consulting</p>
  </section>

  <section class="card card-back">
    <p class="brand-line">Mara Quillon<br>Consulting, LLC</p>

    <div class="person">
      <p class="person-name">MARA QUILLON</p>
      <p class="person-role">Owner</p>
    </div>

    <ul class="contact-list">
      <li>
        <svg viewBox="0 0 16 16"><path d="M3 1h3l1.5 4-2 1.3a9 9 0 0 0 4.2 4.2L11 8.5l4 1.5v3a2 2 0 0 1-2 2A12 12 0 0 1 1 3a2 2 0 0 1 2-2z"/></svg>
        555-014-2290
      </li>
      <li>
        <svg viewBox="0 0 16 16"><path d="M1 3h14v10H1z M2 4l6 5 6-5" stroke="#202123" stroke-width="1.2"/></svg>
        mara@maraquillonconsulting.com
      </li>
      <li>
        <svg viewBox="0 0 16 16"><circle cx="8" cy="8" r="7"/><path d="M1 8h14M8 1c-3 3-3 11 0 14M8 1c3 3 3 11 0 14" stroke="#202123" stroke-width="1" fill="none"/></svg>
        www.maraquillonconsulting.com
      </li>
    </ul>

    <svg class="bottom-bands" viewBox="0 0 640 100" aria-hidden="true">
      <polygon class="band-light" points="0,10 260,40 260,52 0,22" fill="#b9babb"/>
      <path d="M240,100 L262,46 Q268,34 282,36 L640,80 L640,100 Z" fill="#3d4246"/>
    </svg>
    <p class="band-label">Mara Quillon Consulting, LLC</p>
  </section>
</body>
</html>
```